New LLC consulting company needs a business card design

I need a business card design for new company in Alexandria Virginia called TK Verdane Consulting LLC. The company is focused on consulting for defense and national security issues with expertise in nuclear and space topics. I would like to see designs that are simple and I am open to colors except for brown.

Target Market(s)

All businesses that are seeking consulting help

Industry/Entity Type

Consulting

Contact Information for Business Card

Name of company - TK Verdane Consulting LLC; name (Delia Pratt) President; email: prattdq47@mailvessa.com; Phone: 703-555-0142

Requirements
Must have
• The details described above
Nice to have
• I'm open to all ideas
Should not have
• No brown

```html
<!DOCTYPE html>
<html lang="en">
<head>
<meta charset="utf-8">
<title>Delia Pratt — TK Verdane Consulting LLC</title>
<link rel="stylesheet" href="https://fonts.googleapis.com/css2?family=Montserrat:wght@400;700&display=swap">
<style>
  :root {
    --backdrop: #989898;
    --card-blue: #388bcb;
    --ink-white: #ffffff;
  }
  * { margin: 0; padding: 0; box-sizing: border-box; }
  html, body {
    width: 1200px;
    height: 1059px;
    overflow: hidden;
    background: var(--backdrop);
  }
  .canvas {
    position: relative;
    width: 1200px;
    height: 1059px;
  }
  .business-card {
    position: absolute;
    left: 234px;
    top: 320px;
    width: 733px;
    height: 420px;
    border-radius: 26px;
    background: var(--card-blue);
    color: var(--ink-white);
    font-family: "Montserrat", sans-serif;
  }
  .company-name {
    position: absolute;
    left: 37px;
    top: 52px;
    font-size: 18px;
    font-weight: 700;
    letter-spacing: 1.5px;
    text-transform: uppercase;
    line-height: 1;
    white-space: nowrap;
  }
  .person-name {
    position: absolute;
    left: 37px;
    top: 124px;
    font-size: 31px;
    font-weight: 700;
    letter-spacing: 0.1px;
    line-height: 1;
    white-space: nowrap;
  }
  .person-title {
    position: absolute;
    left: 37px;
    top: 170px;
    font-size: 18px;
    font-weight: 400;
    line-height: 1;
  }
  .divider {
    position: absolute;
    left: 39px;
    top: 212px;
    width: 655px;
    height: 1.5px;
    background: var(--ink-white);
  }
  .contact-list {
    position: absolute;
    left: 39px;
    top: 233px;
    list-style: none;
  }
  .contact-item {
    display: flex;
    align-items: center;
    height: 24px;
    margin-bottom: 10px;
    font-size: 18px;
    font-weight: 400;
    line-height: 1;
    white-space: nowrap;
  }
  .contact-icon {
    width: 16px;
    height: 16px;
    margin-right: 8px;
    flex: none;
  }
</style>
</head>
<body>
<div class="canvas">
  <section class="business-card">
    <p class="company-name">TK Verdane Consulting LLC</p>
    <h1 class="person-name">Delia Pratt</h1>
    <p class="person-title">President</p>
    <div class="divider"></div>
    <ul class="contact-list">
      <li class="contact-item">
        <svg class="contact-icon" viewBox="0 0 16 16" aria-hidden="true">
          <rect x="0.5" y="3" width="15" height="10" fill="#fff"/>
          <path d="M0.5 3 L8 9 L15.5 3" fill="none" stroke="#388bcb" stroke-width="1.3"/>
          <path d="M0.5 13 L6 8 M15.5 13 L10 8" fill="none" stroke="#388bcb" stroke-width="1"/>
        </svg>
        <span>prattdq47@mailvessa.com</span>
      </li>
      <li class="contact-item">
        <svg class="contact-icon" viewBox="0 0 16 16" aria-hidden="true">
          <path d="M3.2 1.5 L5.6 4.6 L4.3 6.2 C5.1 8 6.6 9.6 8.6 10.6 L10.2 9.3 L13.4 11.6 L12 14 C7 14.2 1.6 8.6 1.6 3.4 Z" fill="#fff"/>
          <path d="M9 4.2 A3.2 3.2 0 0 1 11.8 7" fill="none" stroke="#fff" stroke-width="1.2" stroke-linecap="round"/>
          <path d="M9.2 1.5 A5.8 5.8 0 0 1 14.5 6.8" fill="none" stroke="#fff" stroke-width="1.2" stroke-linecap="round"/>
        </svg>
        <span>703-555-0142</span>
      </li>
    </ul>
  </section>
</div>
</body>
</html>
```